New Webpage for High Class Expert Witness Services Company

We are looking for a minimalist design for a webpage that just has our logo and an entry form offer to connect with one of our Liaisons.
The entry form should just ask for Name, Email, Contact Info and Description of Project.

Company Name is: The Marlowe Crest Advisory Services

Number of Pages Required

1 page

```html
<!DOCTYPE html>
<html lang="en">
<head>
<meta charset="utf-8">
<title>The Marlowe Crest Advisory Services</title>
<link href="https://fonts.googleapis.com/css2?family=Lora:wght@600&family=Poppins:wght@400;600&display=swap" rel="stylesheet">
<style>
  :root {
    --page-bg: #0a0a0a;
    --hero-dark: #0c0c0c;
    --hero-mid: #232323;
    --text-light: #ffffff;
    --brand-silver: #d9d9d9;
    --field-bg: #f1f1f1;
    --field-bg-bright: #ffffff;
    --placeholder: #6f6f6f;
    --button-bg: #151515;
  }
  * { box-sizing: border-box; margin: 0; padding: 0; }
  html, body { width: 1200px; height: 788px; overflow: hidden; background: var(--page-bg); }
  .page { position: relative; width: 1200px; height: 788px; background: radial-gradient(ellipse at 80% 40%, #141414 0%, var(--page-bg) 70%); font-family: "Poppins", sans-serif; color: var(--text-light); }

  .hero-visual {
    position: absolute; left: 0; top: 0; width: 622px; height: 788px;
    background:
      radial-gradient(ellipse at 40% 60%, var(--hero-mid) 0%, transparent 60%),
      linear-gradient(180deg, #111 0%, #1a1a1a 45%, #202020 75%, var(--hero-dark) 100%);
  }
  .brand {
    position: absolute; left: 116px; top: 204px;
    display: flex; align-items: center; gap: 14px;
  }
  .brand-square { width: 44px; height: 44px; background: var(--brand-silver); }
  .brand-name {
    font-family: "Lora", serif; font-weight: 600; color: var(--brand-silver);
    font-size: 27px; line-height: 30px; letter-spacing: 1px; text-transform: uppercase;
  }

  .contact-panel { position: absolute; left: 725px; top: 150px; width: 378px; }
  .contact-title {
    font-family: "Lora", serif; font-weight: 600; font-size: 29px; line-height: 29px;
    text-transform: uppercase; margin-bottom: 31px;
  }
  .field-label { display: block; font-weight: 600; font-size: 12px; line-height: 14px; text-transform: uppercase; margin-bottom: 7px; }
  .field-input {
    display: block; width: 378px; height: 42px; border: 0; padding-left: 21px;
    background: linear-gradient(90deg, var(--field-bg), var(--field-bg-bright));
    font-family: "Poppins", sans-serif; font-size: 12px; color: #333; margin-bottom: 19px;
  }
  .field-input::placeholder { color: var(--placeholder); }
  .field-textarea { height: 101px; resize: none; padding-top: 12px; background: var(--field-bg-bright); margin-bottom: 12px; }
  .submit-button {
    display: block; width: 378px; height: 42px; border: 0; background: var(--button-bg);
    color: var(--text-light); font-family: "Poppins", sans-serif; font-weight: 600; font-size: 11px;
    text-transform: uppercase;
  }
  .copyright {
    position: absolute; left: 725px; width: 378px; top: 722px; text-align: center;
    font-weight: 600; font-size: 14px;
  }
</style>
</head>
<body>
<main class="page">
  <div class="hero-visual" role="img" aria-label="Dark monochrome photo of a tank and soldiers walking through dust"></div>
  <div class="brand">
    <span class="brand-square"></span>
    <span class="brand-name">Marlowe Crest<br>Advisory Services</span>
  </div>

  <section class="contact-panel">
    <h1 class="contact-title">The Marlowe Crest<br>Advisory Services</h1>
    <form>
      <label class="field-label" for="name">Name</label>
      <input class="field-input" id="name" type="text" placeholder="Johny Smith">
      <label class="field-label" for="email">Email</label>
      <input class="field-input" id="email" type="email" placeholder="Johny@email.com">
      <label class="field-label" for="contact">Contact Info</label>
      <input class="field-input" id="contact" type="text" placeholder="+081 123456789">
      <label class="field-label" for="project">Description of Project</label>
      <textarea class="field-input field-textarea" id="project"></textarea>
      <button class="submit-button" type="button">Connect With Us</button>
    </form>
  </section>

  <p class="copyright">Copyright 2026 | All Rights Reserved</p>
</main>
</body>
</html>
```